Business card design for holistic health care clinic

We need a double-sided business card design for our holistic health care clinic that integrates our logo design and also its color scheme. My business is called Valmira. It is an integrative medicine clinic. You have already done the logo for me. Please ensure an elegant and upscale design that is not cluttered, but still has all the necessary information (please see below for details).

Target Market(s)

Wellness, fitness, rehabilitation for educated, well-traveled open-minded clients who are focused on natural, organic, balanced and preventive healthcare and lifestyle.

Industry/Entity Type

Medical

Contact Information for Business Card

Modern, clean.

Number of Pages Required

1 page

Font styles to use
Serif
Sans Serif

Colors

Designer to choose colors to be used in the design.

Requirements
Must have
• Logo on one side, all other information on the other side.
• Other information should include:
• Tobias Wrenfeld - DOE, CPT, LMT
• 4100 East Marrow Drive
• Austin, TX 78119
• 512 555 0148
• 818 555 0192
• info@ValmiraHealth.example
• t.wrenfeld@ValmiraHealth.example
Nice to have
• Darker background on front - but not totally black - shaded/dark gray.

```html
<!DOCTYPE html>
<html lang="en">
<head>
<meta charset="utf-8">
<title>Valmira Business Card</title>
<link href="https://fonts.googleapis.com/css2?family=Nunito:wght@800&family=Roboto:wght@400&family=Roboto+Condensed:wght@700&display=swap" rel="stylesheet">
<style>
  :root {
    --page: #e6e6e6;
    --charcoal: #2b2b2b;
    --ink: #262626;
    --blue: #0a90d0;
    --blue-deep: #0778ae;
    --white: #ffffff;
  }
  * { margin: 0; padding: 0; box-sizing: border-box; }
  html, body { width: 1200px; height: 960px; overflow: hidden; }
  body { background: var(--page); position: relative; font-family: "Roboto", sans-serif; }

  .card { position: absolute; width: 602px; height: 343px; overflow: hidden; }
  .card--front { left: 314px; top: 113px; background: var(--charcoal); }
  .card--back { left: 311px; top: 472px; width: 600px; background: var(--blue); }

  .card__wave { position: absolute; inset: 0; width: 100%; height: 100%; }

  .brand { position: absolute; font-family: "Nunito", sans-serif; font-weight: 800; letter-spacing: 1px; line-height: 1; }
  .brand--front { left: 48px; top: 80px; font-size: 52px; color: var(--blue); }
  .brand--back { left: 0; right: 0; top: 146px; text-align: center; font-size: 60px; color: var(--ink); }

  .tagline { position: absolute; font-family: "Nunito", sans-serif; font-weight: 800; line-height: 1; }
  .tagline--front { left: 52px; top: 130px; font-size: 15.5px; color: var(--blue); }
  .tagline--back { left: 0; right: 0; top: 210px; text-align: center; font-size: 17px; color: var(--ink); }

  .address { position: absolute; left: 49px; top: 182px; color: var(--white); font-size: 14.5px; line-height: 19px; font-style: normal; }

  .contact-list { position: absolute; left: 50px; top: 229px; list-style: none; color: var(--white); font-size: 14.5px; }
  .contact-list li { display: flex; align-items: center; height: 19px; }
  .contact-list svg { width: 13px; height: 13px; margin-right: 9px; fill: var(--blue); flex: none; }

  .person { position: absolute; right: 50px; top: 266px; text-align: right; color: var(--charcoal); font-family: "Roboto Condensed", sans-serif; font-weight: 700; }
  .person__name { font-size: 20px; line-height: 22px; white-space: nowrap; }
  .person__credentials { font-size: 12px; line-height: 16px; }

  .slogan { position: absolute; left: 0; right: 0; top: 292px; text-align: center; color: var(--ink); font-size: 14px; }
</style>
</head>
<body>

<section class="card card--front">
  <svg class="card__wave" viewBox="0 0 602 343" aria-hidden="true">
    <path fill="var(--blue)" d="M596 0 C585 60 560 80 520 95 C470 115 462 150 460 178 C450 215 395 235 375 268 C360 300 335 335 290 343 L602 343 L602 0 Z"/>
  </svg>
  <svg class="card__wave" viewBox="0 0 602 343">
    <path role="img" aria-label="Lion head silhouette illustration" fill="var(--blue-deep)" d="M420 150 C440 135 470 138 485 160 C500 180 506 200 498 214 C480 220 455 210 440 196 C425 185 412 165 420 150 Z"/>
  </svg>

  <div class="brand brand--front">VALMIRA</div>
  <div class="tagline tagline--front">Integrative Holistic Medicine</div>

  <address class="address">4100 East Marrow Drive<br>Austin, TX 78119</address>

  <ul class="contact-list">
    <li><svg viewBox="0 0 16 16"><path d="M3.5 1 L6 1 L7 5 L5 6.5 C6 9 7 10 9.5 11 L11 9 L15 10 L15 12.5 C15 14 14 15 12.5 15 C6.5 15 1 9.5 1 3.5 C1 2 2 1 3.5 1 Z"/></svg>512 555 0148</li>
    <li><svg viewBox="0 0 16 16"><path d="M4 0 H12 A1.5 1.5 0 0 1 13.5 1.5 V14.5 A1.5 1.5 0 0 1 12 16 H4 A1.5 1.5 0 0 1 2.5 14.5 V1.5 A1.5 1.5 0 0 1 4 0 Z M4.5 2 V12.5 H11.5 V2 Z M8 13.2 A0.9 0.9 0 1 0 8 15 A0.9 0.9 0 1 0 8 13.2 Z"/></svg>818 555 0192</li>
    <li><svg viewBox="0 0 16 16"><path d="M1 3 H15 V13 H1 Z M2 4 L8 9 L14 4 Z" fill-rule="evenodd"/></svg>info@ValmiraHealth.example</li>
    <li><svg viewBox="0 0 16 16"><path d="M1 3 H15 V13 H1 Z M2 4 L8 9 L14 4 Z" fill-rule="evenodd"/></svg>t.wrenfeld@ValmiraHealth.example</li>
    <li><svg viewBox="0 0 16 16"><circle cx="8" cy="8" r="7"/><path d="M1 8 H15 M8 1 C5 4 5 12 8 15 M8 1 C11 4 11 12 8 15" stroke="var(--charcoal)" stroke-width="1.2" fill="none"/></svg>www.ValmiraHealth.example</li>
  </ul>

  <div class="person">
    <div class="person__name">TOBIAS WRENFELD</div>
    <div class="person__credentials">DOE, CPT, LMT</div>
  </div>
</section>

<section class="card card--back">
  <div class="brand brand--back">VALMIRA</div>
  <div class="tagline tagline--back">Integrative Holistic Medicine</div>
  <p class="slogan">it’s all about you — your health, your objectives</p>
</section>

</body>
</html>
```